Martin R Cole DDS (dentist) needs a business card/business logo design

I would like an eye-catchingly conservative or elegant graphic presentation of my business name with the elements: prevention, restoration, and cosmetics (these are the services I'd like to emphasize) .
The business card would have room for address lines, phone and fax, web address. No standard teeth or oral representations please. Should communicate professionalism. Whatever color scheme works.

Thank you

Target Market(s)

I just want a good looking business card

Industry/Entity Type

Conservative

Contact Information for Business Card

Adress: 4163 Brisdale Ave Fernhill OR 97648 Phone: 555 419 3086 FAX 555 419 5274 Web: Fernhilldental.com

Font styles to use
Sans Serif

Colors
0255a3

Requirements
Must have
• business name with the elements: prevention, restoration, and cosmetics (these are the services I'd like to emphasize)
• communicates professionalism
Nice to have
• eye catching but not flashy graphics
Should not have
• no pictures of teeth or dental instruments

```html
<!DOCTYPE html>
<html lang="en">
<head>
<meta charset="utf-8">
<title>Martin R Cole DDS – Business Card</title>
<link rel="stylesheet" href="https://fonts.googleapis.com/css2?family=Ubuntu:wght@400;500;700&display=swap">
<style>
  :root {
    --green: #86c63a;
    --green-dark: #78bb2a;
    --white: #ffffff;
    --backdrop: #e9eaec;
  }
  * { box-sizing: border-box; margin: 0; padding: 0; }
  html, body {
    width: 1200px; height: 1000px; overflow: hidden;
    background: var(--backdrop);
  }
  .card {
    position: absolute; left: 100px; top: 210px;
    width: 1000px; height: 580px;
    background: linear-gradient(135deg, var(--green) 0%, var(--green-dark) 100%);
    font-family: "Ubuntu", sans-serif;
    box-shadow: 0 6px 24px rgba(0,0,0,.18);
    overflow: hidden;
  }
  .panel-top {
    position: absolute; left: 0; top: 0;
    width: 580px; height: 210px; background: var(--white);
  }
  .panel-main {
    position: absolute; left: 0; top: 200px;
    width: 530px; height: 380px; background: var(--white);
  }
  .name-bar {
    position: absolute; left: 30px; top: 90px;
    width: 600px; height: 145px; background: var(--green);
    color: var(--white); text-align: center;
    display: flex; flex-direction: column; justify-content: center;
    padding-right: 40px;
  }
  .name-bar .name { font-weight: 700; font-size: 36px; }
  .name-bar .role { font-weight: 400; font-size: 26px; margin-top: 4px; }
  .contacts {
    position: absolute; left: 22px; color: var(--green-dark);
    font-size: 27px; font-weight: 500; list-style: none;
    white-space: nowrap;
  }
  .contacts li { display: flex; align-items: center; gap: 10px; height: 40px; }
  .contacts svg { width: 32px; height: 32px; flex: none; }
  .contacts.phones { top: 272px; }
  .contacts.online { top: 395px; font-weight: 400; font-size: 25px; }
  .brand {
    position: absolute; left: 530px; top: 300px; width: 470px;
    color: var(--white); text-align: center;
  }
  .brand .brand-name {
    font-weight: 700; font-size: 40px; letter-spacing: 1px;
    display: flex; align-items: center; justify-content: center; gap: 12px;
    white-space: nowrap;
  }
  .brand .brand-mark { width: 16px; height: 16px; border-radius: 50%; background: var(--white); }
  .brand .services {
    font-weight: 500; font-size: 23px; margin-top: 16px;
    white-space: nowrap;
  }
</style>
</head>
<body>
  <article class="card">
    <div class="panel-top"></div>
    <div class="panel-main"></div>

    <header class="name-bar">
      <span class="name">Martin R Cole DDS</span>
      <span class="role">Dentist</span>
    </header>

    <ul class="contacts phones">
      <li>
        <svg viewBox="0 0 32 32" aria-hidden="true"><path fill="currentColor" d="M4 11c0-4 5-6 12-6s12 2 12 6v2h-6v-3c-2-1-10-1-12 0v3H4zM9 15h14l3 10H6z"/><circle cx="16" cy="20" r="3" fill="#fff"/></svg>
        : 555- 419- 3086
      </li>
      <li>
        <svg viewBox="0 0 32 32" aria-hidden="true"><path fill="currentColor" d="M9 4h14v7H9zM4 12h24v12h-5v-4H9v4H4zM10 21h12v8H10z"/><rect x="12" y="23" width="8" height="1.5" fill="#fff"/><rect x="12" y="26" width="8" height="1.5" fill="#fff"/></svg>
        : 555- 419- 5274
      </li>
    </ul>

    <ul class="contacts online">
      <li>
        <svg viewBox="0 0 32 32" aria-hidden="true"><circle cx="16" cy="16" r="14" fill="currentColor"/><text x="16" y="19.5" text-anchor="middle" font-size="9" font-family="Ubuntu, sans-serif" font-weight="700" fill="#fff">www</text></svg>
        : www.Fernhilldental.com
      </li>
      <li>
        <svg viewBox="0 0 32 32" aria-hidden="true"><path fill="none" stroke="currentColor" stroke-width="2" d="M3 28l5-8h16l5 8z"/><path fill="currentColor" d="M16 2a7 7 0 0 1 7 7c0 5-7 12-7 12S9 14 9 9a7 7 0 0 1 7-7z"/><circle cx="16" cy="9" r="2.5" fill="#fff"/></svg>
        : 4163 Brisdale Ave, Fernhill, OR 97648
      </li>
    </ul>

    <section class="brand">
      <div class="brand-name"><span class="brand-mark"></span>Martin R Cole DDS</div>
      <div class="services">Prevention, Restoration and Cosmetics</div>
    </section>
  </article>
</body>
</html>
```